Brightcoat Painting Services Requires a New Responsive Site

Hi Designers,

Our current website is this www.brightcoatpainting.com.au for some idea.
I made it on Adobe Muse, its very basic.
I would like it to be redesigned to look more professional and also responsive. I actually know how to do html5 and css but I think others will do this much better than me.

I do not need content because I am a copywriter and would like to do all SEO and copy myself.

The most improtant things to remember is that the site cannot use a CMS
and the code needs to be understandable so that I can go in and add content later on and do SEO work.

Also the site requires an additional testimonial page. I would imagine a nice gallery would be a great addition too(something that I can add images too through html. Also in it is important for it to contain those brand images on the front page as it increases authority. I will attach them onto the brief.

Those two files of nearbyfind and tradeleafs are local directories where we have reviews so a placement of those on the testimonail page would make great sense. I will to the href myself.

Anyway, good luck!

I look forward to see your designs :D
Updates

I have just been informed that on this site websites are simply designed and not built (developed) if this is the case please stop working on your designs and spending more time on this project. I REQUIRE DEVELOPMENT ALSO AND HAVE ALREADY CONTACTED SUPPORT.

Target Market(s)

The target market is 30-75 high income earners.

Industry/Entity Type

Painting

Number of Pages Required

5+ page

Font styles to use
Serif
Sans Serif

Requirements
Must have
• attractive gallery, and the brand icons uploaded.
• must be responsive
• web carousel (with the different types of work we do). eg domestic, commercial, industrial etc.
Nice to have
• a little interactivity
• corporate a natural design that goes well with our logo
Should not have
• any content. just write jiberish to fill in the spaces.
• I will be doing all copy and SEO myself.
• More than five pages, bascially the four that already exist plus the testimonail one.

```html
<!DOCTYPE html>
<html lang="en">
<head>
<meta charset="utf-8">
<title>Brightcoat Painting</title>
<link href="https://fonts.googleapis.com/css2?family=Open+Sans:ital,wght@0,400;0,600;0,700;1,400&display=swap" rel="stylesheet">
<style>
:root{
  --blue:#3aaee9;
  --text:#6b6b6b;
  --dark:#333;
  --footer:#363636;
  --footer-text:#e6e6e6;
  --line:#e2e2e2;
  --neutral:#d6d6d6;
  --white:#fff;
}
*{margin:0;padding:0;box-sizing:border-box}
html,body{width:1200px;height:2675px;overflow:hidden;background:var(--white);font-family:"Open Sans",Arial,sans-serif;color:var(--text)}
.page{position:relative;width:1200px;height:2675px}
.abs{position:absolute}
.brand-mark{left:107px;top:24px;width:92px;height:86px;background:var(--blue);border-radius:4px}
.brand-name{left:219px;top:48px;font-size:25px;font-weight:600;color:var(--dark)}
.call{right:107px;top:14px;font-size:23px;font-weight:600;color:var(--blue)}
.nav{right:107px;top:72px;display:flex;gap:52px;font-size:15px;color:var(--text)}
.nav .active{color:var(--blue)}
.hero{left:107px;top:134px;width:984px;height:563px;background:linear-gradient(90deg,#9fc7d6 0%,#e9eef1 45%,#f6f8fa 70%,#fdfdfd 100%);box-shadow:0 10px 14px -10px rgba(0,0,0,.35)}
.hero-title{left:642px;top:292px;font-size:46px;font-weight:600;color:var(--blue)}
.hero-text{left:643px;top:366px;width:450px;font-size:15px;line-height:30px;color:var(--text)}
.dots{left:1002px;top:630px;display:flex;gap:4px}
.dots span{width:12px;height:12px;border-radius:50%;background:#333}
.dots span:first-child{background:var(--blue)}
.heading{left:0;width:1200px;text-align:center;font-size:28px;font-weight:600;color:var(--blue)}
.intro{left:90px;width:1020px;top:793px;text-align:center;font-size:14.5px;line-height:25px}
.service{top:873px;width:240px;text-align:center}
.service .disc{width:154px;height:154px;border-radius:50%;background:var(--blue);margin:0 auto;display:flex;align-items:center;justify-content:center}
.service h3{margin-top:30px;font-size:20px;font-weight:400;color:var(--blue)}
.service p{width:184px;margin:10px auto 0;font-size:15px;line-height:24px}
.gallery{left:107px;top:1271px;width:984px;height:432px;display:grid;grid-template-columns:repeat(3,1fr);grid-template-rows:1fr 1fr;gap:3px}
.gallery div{width:100%;height:100%}
.testimonial-photo{left:562px;top:1819px;width:74px;height:74px;border-radius:50%;background:#8a7660}
.arrow{top:1836px}
.quote{left:140px;width:920px;top:1905px;text-align:center;font-style:italic;font-size:15px;line-height:24px}
.clients{left:110px;top:2088px;display:flex;gap:15px}
.client{width:185px;height:125px;border:1px solid var(--line);display:flex;align-items:center;justify-content:center;gap:8px;font-size:20px;font-weight:700;color:var(--dark)}
.client i{display:block;width:18px;height:18px;border-radius:50%;background:var(--blue)}
.client .placeholder{width:60px;height:60px;background:var(--neutral)}
.footer{left:0;top:2291px;width:1200px;height:384px;background:var(--footer)}
.fcol{top:2325px;color:var(--footer-text);font-size:14px;line-height:28px}
.fcol h4{font-size:20px;font-weight:600;color:var(--blue);margin-bottom:8px;line-height:26px}
.fcol .more{color:var(--blue);margin-top:8px}
.divider{left:107px;top:2546px;width:984px;height:1px;background:#4a4a4a}
.bottom-links{left:107px;top:2574px;font-size:13px;color:var(--footer-text);word-spacing:2px}
.bottom-links b{font-weight:400;margin:0 14px}
.copyright{left:107px;top:2627px;font-size:13px;color:var(--footer-text)}
.social{left:893px;top:2578px;display:flex;gap:9px}
.social span{width:33px;height:33px;border-radius:50%;background:var(--white)}
</style>
</head>
<body>
<div class="page">
  <header>
    <div class="abs brand-mark"></div>
    <div class="abs brand-name">Brightcoat Painting</div>
    <div class="abs call">Call Us : 1300 555 214</div>
    <nav class="abs nav"><span class="active">Home</span><span>Services</span><span>About Us</span><span>Gallery</span><span>Contact Us</span></nav>
  </header>

  <section>
    <div class="abs hero" role="img" aria-label="Carousel photo of a smiling woman painting a wall with a blue brush"></div>
    <h1 class="abs hero-title">Brightcoat Painting</h1>
    <p class="abs hero-text">Brightcoat Painting Services is a Melbourne family owned Painting &amp; Decorating business based in Eastvale, in the south east of Melbourne.</p>
    <div class="abs dots"><span></span><span></span><span></span><span></span></div>
  </section>

  <section>
    <h2 class="abs heading" style="top:743px">Quality And Service</h2>
    <p class="abs intro">Brightcoat Painting Services is a Melbourne family owned Painting &amp; Decorating business based in Eastvale, in the south east of Melbourne.<br>We proudly provide domestic and commercial painting services across all suburbs of metropolitan Melbourne.</p>

    <div class="abs service" style="left:69px">
      <div class="disc"><svg width="70" height="70" viewBox="0 0 70 70"><path d="M35 6 4 34h9v30h17V46h10v18h17V34h9z" fill="#fff"/></svg></div>
      <h3>Domestic</h3><p>At brightcoat painting we are focused on superior quality</p>
    </div>
    <div class="abs service" style="left:347px">
      <div class="disc"><svg width="70" height="70" viewBox="0 0 70 70" fill="#fff"><rect x="12" y="22" width="18" height="42"/><rect x="32" y="8" width="26" height="56"/><g fill="#3aaee9"><rect x="16" y="28" width="4" height="5"/><rect x="23" y="28" width="4" height="5"/><rect x="16" y="38" width="4" height="5"/><rect x="23" y="38" width="4" height="5"/><rect x="37" y="14" width="5" height="6"/><rect x="48" y="14" width="5" height="6"/><rect x="37" y="26" width="5" height="6"/><rect x="48" y="26" width="5" height="6"/><rect x="37" y="38" width="5" height="6"/><rect x="48" y="38" width="5" height="6"/></g></svg></div>
      <h3>Commercial</h3><p>At brightcoat painting we are focused on superior quality</p>
    </div>
    <div class="abs service" style="left:618px">
      <div class="disc"><svg width="76" height="70" viewBox="0 0 76 70"><path d="M6 64V14h10v22l16-10v10l16-10v10l16-10v38z" fill="#fff"/><g fill="#3aaee9"><rect x="16" y="46" width="7" height="6"/><rect x="30" y="46" width="7" height="6"/><rect x="44" y="46" width="7" height="6"/><rect x="56" y="46" width="5" height="6"/></g></svg></div>
      <h3>Industrial</h3><p>At brightcoat painting we are focused on superior quality</p>
    </div>
    <div class="abs service" style="left:891px">
      <div class="disc"><svg width="72" height="70" viewBox="0 0 72 70" fill="#fff"><path d="M36 6 6 22v5h60v-5z"/><rect x="12" y="31" width="7" height="24"/><rect x="25" y="31" width="7" height="24"/><rect x="40" y="31" width="7" height="24"/><rect x="53" y="31" width="7" height="24"/><rect x="6" y="58" width="60" height="6"/></svg></div>
      <h3>Heritage</h3><p>At brightcoat painting we are focused on superior quality</p>
    </div>
  </section>

  <section>
    <h2 class="abs heading" style="top:1212px">Our Gallery</h2>
    <div class="abs gallery">
      <div role="img" aria-label="Colour swatches on a white wall with a green ladder" style="background:linear-gradient(#f2f0ee,#d9d6d2)"></div>
      <div role="img" aria-label="Painter rolling a wall beside a window" style="background:linear-gradient(135deg,#cfc6b6,#8f8a7c)"></div>
      <div role="img" aria-label="Room with a dark blue feature wall and artwork" style="background:linear-gradient(#d8c9a8,#4c5a6e)"></div>
      <div role="img" aria-label="Room with a purple feature wall" style="background:linear-gradient(90deg,#d9cfc9,#7e4c5c)"></div>
      <div role="img" aria-label="Painter rolling bright blue paint onto a wall" style="background:linear-gradient(90deg,#e6eef2,#2f86c6)"></div>
      <div role="img" aria-label="Timber floored room with glass doors" style="background:linear-gradient(#a9553e,#5a2b1c)"></div>
    </div>
  </section>

  <section>
    <h2 class="abs heading" style="top:1759px">Testimonials</h2>
    <svg class="abs arrow" style="left:405px" width="20" height="38" viewBox="0 0 20 38"><path d="M18 2 2 19l16 17" fill="none" stroke="#cfcfcf" stroke-width="2"/></svg>
    <div class="abs testimonial-photo" role="img" aria-label="Customer portrait"></div>
    <svg class="abs arrow" style="left:757px" width="20" height="38" viewBox="0 0 20 38"><path d="M2 2l16 17L2 36" fill="none" stroke="#cfcfcf" stroke-width="2"/></svg>
    <p class="abs quote">“ Lorem ipsum dolor sit amet, solet epicurei interesset vis ne. Quot placerat adipisci in quo, an vel tamquam tibique epicuri, sit summo facilisi at. Ad clita disputando vis, posse aliquam philosophia mel ea. Mea te omnes facilisis, per ut omnes mediocrem, eu choro abhorreant ius. ”</p>
  </section>

  <section>
    <h2 class="abs heading" style="top:2020px">Our Clients</h2>
    <div class="abs clients">
      <div class="client"><i></i>Tintwell</div>
      <div class="client">Velvane</div>
      <div class="client"><i></i>nearbyfind</div>
      <div class="client"><span class="placeholder" role="img" aria-label="Workmanship guarantee badge"></span></div>
      <div class="client">Hartmere</div>
    </div>
  </section>

  <footer>
    <div class="abs footer"></div>
    <div class="abs fcol" style="left:107px;width:260px">
      <h4>About Us</h4>
      <p>Id adipisci indoctum pro. Vis magna dicat sensibus ei. Quo ad labores patrioque, modo persequeris vel ad. Quo ad labores patrioque.</p>
      <p class="more">Read More</p>
    </div>
    <div class="abs fcol" style="left:424px"><h4>Services</h4><p>Commercial<br>Domestic<br>Industrial<br>Heritage</p></div>
    <div class="abs fcol" style="left:583px"><h4>Quick Links</h4><p>About Us<br>Services<br>Gallery<br>Contact Us</p></div>
    <div class="abs fcol" style="left:761px"><h4>Contact Us</h4><p>Address: Eastvale, Victoria 3999,<br>Australia<br>Email: info@brightcoatpainting.com.au<br>Phone: 1300 555 214</p></div>
    <div class="abs divider"></div>
    <div class="abs bottom-links">Home<b>|</b>About Us<b>|</b>Services<b>|</b>Gallery<b>|</b>Contact Us</div>
    <div class="abs social"><span></span><span></span><span></span><span></span><span></span></div>
    <div class="abs copyright">Copyright @ 2014 BrightcoatPainting.All Rights Reserved.</div>
  </footer>
</div>
</body>
</html>
```